Business Cards for IT Consulting Company (Managed Service Provider)

I am looking to have some business cards printed and would like some designs. We are an IT Consulting company based in Vancouver BC. I would like a nice clean and modern look to the cards. I have uploaded all the versions of my logo so parts can be used as needed. Here is a snippit from our website homepage:

Quillbrook Networks Ltd. is an IT Solutions Partner located in Vancouver BC, Canada. We offer IT solutions and support to customers in the greater Vancouver Area. With expertise in Microsoft platforms, as well as Linux and Mac OSX and over 12 years experience in the IT industry, Quillbrook Networks is dedicated to offering our clients top quality service and products. We take pride in the solutions we offer our customers. The greatest compliment a client can give us is to recommend our services.

Quillbrook Networks Ltd. offers a wide range of IT services from onsite service to remote support and managed service solutions. This allows clients to choose the support path that best suits their company’s needs. Supporting many different sized companies from small to enterprise level over the past 12 years Quillbrook Networks has the experience and expertise needed to ensure things run smoothly. Allowing our clients to focus on doing business.

Revolutionizing the way IT services are delivered.

Quillbrook Networks is dedicated to providing our clients with IT solutions that work and grow with them for years to come. This philosophy helps save money in the long run instead of replacing equipment constantly. Far too often IT solutions are not well thought out and while possibly solving the problem at hand, require replacement due to growth or quality within a very short time frame. Quillbrook Networks takes pride in providing solutions that will last and be able to accommodate growth without the need for replacement.

Industry/Entity Type

Information Technology

Contact Information for Business Card

Quillbrook Networks Ltd.
(Employee Name)
Eml: (Employees Email Address)
Web: quillbrook.me
Ph: 604-555-0148

Font styles to use
Serif
Sans Serif

Requirements
Must have
• The Company logo and company colors.
Nice to have
• - Our tag line: "Revolutionizing IT Services" or "Revolutionizing the way IT services are delivered."
• - Also I really like the idea of nature and technology together blending which is sort of where my logo came from so integrating that somehow onto the business cards would be great.

```html
<!DOCTYPE html>
<html lang="en">
<head>
<meta charset="utf-8">
<title>Quillbrook Networks Ltd. – Business Card</title>
<link rel="stylesheet" href="https://fonts.googleapis.com/css2?family=Montserrat:wght@400;500;700&display=swap">
<style>
  :root {
    --backdrop: #2b2b2b;
    --card-black: #000000;
    --card-white: #ffffff;
    --brand-blue: #1ba1e2;
    --text-grey: #555555;
    --text-light: #ffffff;
  }
  * { box-sizing: border-box; margin: 0; padding: 0; }
  html, body {
    width: 1200px; height: 900px; overflow: hidden;
    background: var(--backdrop);
    font-family: "Montserrat", Arial, sans-serif;
  }
  .canvas { position: relative; width: 1200px; height: 900px; }
  .card {
    position: absolute; left: 340px; width: 520px; height: 300px;
    overflow: hidden;
    box-shadow: 0 12px 30px rgba(0,0,0,0.55);
  }

  /* Back of card */
  .card-back { top: 110px; background: var(--card-black); }
  .card-back .tagline {
    position: absolute; left: 40px; top: 186px;
    color: var(--text-light); font-size: 16px; font-weight: 500; letter-spacing: 0.5px;
  }
  .card-back .brand-square {
    position: absolute; right: 44px; top: 34px; width: 120px; height: 120px;
    border: 4px solid var(--brand-blue);
  }

  /* Front of card */
  .card-front { top: 480px; background: var(--card-white); }
  .card-front .dark-band {
    position: absolute; left: 0; top: 0; width: 100%; height: 160px;
    background: var(--card-black);
  }
  .card-front .wordmark {
    position: absolute; left: 34px; top: 96px;
    display: flex; align-items: center; gap: 14px;
  }
  .card-front .wordmark-square {
    width: 30px; height: 30px; border: 3px solid var(--brand-blue);
  }
  .card-front .wordmark-name {
    color: var(--brand-blue); font-size: 24px; font-weight: 700;
  }
  .card-front .corner-square {
    position: absolute; right: 30px; top: 178px; width: 96px; height: 96px;
    border: 4px solid var(--brand-blue);
  }
  .card-front .contact {
    position: absolute; left: 34px; top: 180px;
  }
  .contact .person-name {
    color: var(--brand-blue); font-size: 20px; font-weight: 700; letter-spacing: 1.5px;
  }
  .contact .person-role {
    color: var(--text-grey); font-size: 12px; font-weight: 500; letter-spacing: 1px;
    margin-bottom: 8px;
  }
  .contact .contact-line {
    display: flex; align-items: center; gap: 10px;
    color: var(--text-grey); font-size: 13px; line-height: 20px; letter-spacing: 0.5px;
  }
  .contact-line svg { width: 12px; height: 12px; flex: none; }
</style>
</head>
<body>
<main class="canvas">
  <section class="card card-back" aria-label="Card back">
    <p class="tagline">Revolutionizing IT Services</p>
    <div class="brand-square"></div>
  </section>

  <section class="card card-front" aria-label="Card front">
    <div class="dark-band"></div>
    <div class="wordmark">
      <span class="wordmark-square"></span>
      <span class="wordmark-name">Quillbrook Networks Ltd.</span>
    </div>
    <div class="corner-square"></div>
    <div class="contact">
      <p class="person-name">TOBIN HARLOW</p>
      <p class="person-role">DIRECTOR</p>
      <p class="contact-line">
        <svg viewBox="0 0 12 12" aria-hidden="true"><path d="M2.5 1 L4.5 1 L5 3.5 L3.8 4.3 Q4.8 6.8 7.7 8.2 L8.5 7 L11 7.5 L11 9.5 Q10.5 11 9 11 Q1 10 1 2.5 Q1 1 2.5 1 Z" fill="var(--brand-blue)"/></svg>
        604-555-0148
      </p>
      <p class="contact-line">
        <svg viewBox="0 0 12 12" aria-hidden="true"><rect x="1" y="2.5" width="10" height="7" fill="none" stroke="var(--brand-blue)" stroke-width="1.2"/><path d="M1 2.5 L6 6.5 L11 2.5" fill="none" stroke="var(--brand-blue)" stroke-width="1.2"/></svg>
        info@tobinharlow.com
      </p>
      <p class="contact-line">
        <svg viewBox="0 0 12 12" aria-hidden="true"><circle cx="6" cy="6" r="5" fill="none" stroke="var(--brand-blue)" stroke-width="1.2"/><ellipse cx="6" cy="6" rx="2.2" ry="5" fill="none" stroke="var(--brand-blue)" stroke-width="1"/><path d="M1 6 H11" stroke="var(--brand-blue)" stroke-width="1"/></svg>
        www.quillbrook.me
      </p>
    </div>
  </section>
</main>
</body>
</html>
```